SLides. Repair phone, tablet, pc, accessories seell and tempered glass.

i would like to show client what we do . what we sell. the repair can be done from 30min. We install tempered glasses. We sell accessories. have already slides. but design not very modern. need to change them. https://filebox.example/folders/7KpQw2XzLm9RtYvBn4HcJd8SfGaEuW3?usp=sharing https://filebox.example/folders/4TzXk-Lp83QnVHcdRw9yFmPoGsa?usp=sharing i send all the design i have. our website is www.nutikoda.ee i uploaded what photos i like.

Target Market(s)

Trade buy repair. phones, taböets, PC, sell accessories. show all services

Colors

Designer to choose colors to be used in the design.

Requirements
Must have
• modern design modern phone pictures. zeno pictures vexa pictures. To emphasize our style.
Nice to have
• modern pictures of our services. and modern pictures of goods.
Should not have
• non modern pictures and

```html
<!DOCTYPE html>
<html lang="et">
<head>
<meta charset="utf-8">
<title>Nutikoda – slaidid</title>
<link href="https://fonts.googleapis.com/css2?family=Exo+2:wght@700;800&family=Oswald:wght@600&family=Fira+Sans:wght@400;500&display=swap" rel="stylesheet">
<style>
  :root {
    --stage: #424242;
    --slide-bg: #e4e0e6;
    --ink: #1b1b1b;
    --teal: #14b8c4;
    --teal-deep: #06afd2;
    --teal-green: #13b3a3;
    --sky: #31c1e3;
    --dark-disc: #222d30;
    --body-text: #333;
    --white: #ffffff;
  }
  * { box-sizing: border-box; margin: 0; padding: 0; }
  html, body { width: 1058px; height: 1200px; overflow: hidden; background: var(--stage); }
  .canvas { position: relative; width: 1058px; height: 1200px; }
  .slide {
    position: absolute; left: 72.5px; width: 907px; height: 484px;
    background: var(--slide-bg); overflow: hidden;
    font-family: "Fira Sans", sans-serif; color: var(--ink);
  }
  .slide--glass { top: 88px; }
  .slide--repair { top: 636px; }
  .slide svg.layer { position: absolute; left: 0; top: 0; width: 907px; height: 484px; }

  .brand {
    position: absolute; display: flex; align-items: center; gap: 8px;
    font-family: "Exo 2", sans-serif; font-weight: 800; color: var(--ink); letter-spacing: -0.5px;
  }
  .brand-mark { background: var(--ink); display: block; }
  .slide--glass .brand { left: 54px; top: 34px; font-size: 32px; }
  .slide--glass .brand-mark { width: 18px; height: 18px; }
  .slide--repair .brand { left: 22px; top: 22px; font-size: 26px; }
  .slide--repair .brand-mark { width: 15px; height: 15px; }

  .headline {
    position: absolute; left: 53px; top: 114px;
    font-family: "Exo 2", sans-serif; font-weight: 800; font-size: 26px; line-height: 30px;
    color: var(--teal-deep); letter-spacing: -0.2px; white-space: nowrap;
  }
  .intro {
    position: absolute; left: 54px; top: 189px;
    font-size: 18px; line-height: 25.5px; color: var(--body-text); white-space: nowrap;
  }

  .disc {
    position: absolute; border-radius: 50%;
    display: flex; align-items: center; justify-content: center; text-align: center;
    font-family: "Oswald", sans-serif; font-weight: 600; line-height: 1.1;
  }
  .disc--sale { left: 514px; top: 50px; width: 112px; height: 112px; background: var(--dark-disc); color: var(--white); font-size: 33px; }
  .disc--repair { left: 643px; top: 14px; width: 120px; height: 120px; background: var(--sky); color: var(--dark-disc); font-size: 29px; }
  .disc--accessories { left: 761px; top: 79px; width: 124px; height: 124px; background: var(--dark-disc); color: var(--white); font-size: 21px; }

  .service-list {
    position: absolute; top: 95px; list-style: none;
    font-size: 13px; line-height: 22px; text-transform: uppercase; color: var(--ink);
  }
  .service-list li { display: flex; align-items: center; gap: 10px; }
  .service-list svg { width: 13px; height: 11px; flex: none; }
  .service-list--a { left: 71px; }
  .service-list--b { left: 269px; }
  .service-list--c { left: 655px; }
  .column-rule { position: absolute; top: 83px; width: 2px; height: 61px; background: rgba(255,255,255,0.7); }

  .feature {
    position: absolute; top: 400px; width: 88px; text-align: center;
    color: var(--white); font-size: 8.5px; letter-spacing: 0.3px;
  }
  .feature svg { display: block; margin: 0 auto 9px; width: 38px; height: 38px; }
  .feature-rule { position: absolute; top: 322px; width: 1px; height: 162px; background: rgba(255,255,255,0.35); }
</style>
</head>
<body>
<main class="canvas">

  <!-- Slide 1: screen protection -->
  <section class="slide slide--glass">
    <svg class="layer" viewBox="0 0 907 484">
      <defs>
        <linearGradient id="bandGlass" x1="0" y1="0" x2="0" y2="1">
          <stop offset="0" stop-color="#1ab4a5"/>
          <stop offset="1" stop-color="#03b0d6"/>
        </linearGradient>
        <linearGradient id="phoneGlass" x1="0" y1="0" x2="1" y2="1">
          <stop offset="0" stop-color="#8a6448"/>
          <stop offset="0.45" stop-color="#1d1512"/>
          <stop offset="0.8" stop-color="#3b2a22"/>
          <stop offset="1" stop-color="#93a3c6"/>
        </linearGradient>
      </defs>
      <path d="M0 287 L500 468 Q560 492 620 465 L907 245 L907 484 L0 484 Z" fill="url(#bandGlass)"/>
      <polygon role="img" aria-label="Photo: smartphone with tempered glass screen protector being applied"
               points="230,340 725,190 800,192 846,218 840,250 560,470 520,465 300,385"
               fill="url(#phoneGlass)"/>
    </svg>

    <div class="brand"><span class="brand-mark"></span>Nutikoda</div>

    <h1 class="headline">KAITSEKILE JA - KLAASI<br>PROFESSIONAALNE PAIGALDUS</h1>
    <p class="intro">Meie poes on lai valik kaiteskile ja<br>klaase. Pakume professionaalse kaitse<br>paigalduse. Osts kaitsekile</p>

    <div class="disc disc--sale">MÜÜK</div>
    <div class="disc disc--repair">REMONT</div>
    <div class="disc disc--accessories">TARVIKUTE<br>MÜÜK</div>
  </section>

  <!-- Slide 2: services -->
  <section class="slide slide--repair">
    <svg class="layer" viewBox="0 0 907 484">
      <defs>
        <radialGradient id="burst" cx="0.5" cy="0.55" r="0.7">
          <stop offset="0" stop-color="#f1eef3"/>
          <stop offset="1" stop-color="#e0dce3"/>
        </radialGradient>
        <linearGradient id="bandRepair" x1="0" y1="0" x2="0" y2="1">
          <stop offset="0" stop-color="#17b2a4"/>
          <stop offset="1" stop-color="#03b0d6"/>
        </linearGradient>
        <linearGradient id="phoneOpen" x1="0" y1="0" x2="1" y2="1">
          <stop offset="0" stop-color="#4a4d52"/>
          <stop offset="0.5" stop-color="#25272b"/>
          <stop offset="0.8" stop-color="#b8bbc0"/>
          <stop offset="1" stop-color="#d9a58f"/>
        </linearGradient>
      </defs>
      <rect width="907" height="484" fill="url(#burst)"/>
      <polygon role="img" aria-label="Photo: hands opening a smartphone to show its internal components for repair"
               points="0,178 560,168 680,200 660,260 520,400 420,484 200,484 0,420"
               fill="url(#phoneOpen)"/>
      <polygon points="266,484 907,295 907,484" fill="url(#bandRepair)"/>
    </svg>

    <div class="brand"><span class="brand-mark"></span>Nutikoda</div>

    <ul class="service-list service-list--a">
      <li><svg viewBox="0 0 13 11"><path d="M1 6 L5 9.5 L12 1.5" fill="none" stroke="#14b0d0" stroke-width="2.6"/></svg>What we do</li>
      <li><svg viewBox="0 0 13 11"><path d="M1 6 L5 9.5 L12 1.5" fill="none" stroke="#14b0d0" stroke-width="2.6"/></svg>What we sell</li>
    </ul>
    <span class="column-rule" style="left:226px"></span>
    <ul class="service-list service-list--b">
      <li><svg viewBox="0 0 13 11"><path d="M1 6 L5 9.5 L12 1.5" fill="none" stroke="#14b0d0" stroke-width="2.6"/></svg>The repair can be done from 30min</li>
      <li><svg viewBox="0 0 13 11"><path d="M1 6 L5 9.5 L12 1.5" fill="none" stroke="#14b0d0" stroke-width="2.6"/></svg>We install tempered glasses</li>
    </ul>
    <span class="column-rule" style="left:594px"></span>
    <ul class="service-list service-list--c">
      <li><svg viewBox="0 0 13 11"><path d="M1 6 L5 9.5 L12 1.5" fill="none" stroke="#14b0d0" stroke-width="2.6"/></svg>We sell accessories</li>
      <li><svg viewBox="0 0 13 11"><path d="M1 6 L5 9.5 L12 1.5" fill="none" stroke="#14b0d0" stroke-width="2.6"/></svg>Motherboard replacement</li>
    </ul>

    <span class="feature-rule" style="left:643px; top:372px; height:112px"></span>
    <span class="feature-rule" style="left:733px; top:345px; height:139px"></span>
    <span class="feature-rule" style="left:820px; top:320px; height:164px"></span>

    <div class="feature" style="left:550px">
      <svg viewBox="0 0 38 38"><circle cx="19" cy="19" r="16" fill="none" stroke="#fff" stroke-width="5"/><path d="M10 28 L22 16" stroke="#fff" stroke-width="5" stroke-linecap="round"/></svg>
      LOREM IPSUM
    </div>
    <div class="feature" style="left:643px">
      <svg viewBox="0 0 38 38"><rect x="5" y="10" width="24" height="22" fill="none" stroke="#fff" stroke-width="2.5"/><line x1="3" y1="34" x2="35" y2="34" stroke="#fff" stroke-width="2.5"/><path d="M18 24 L32 8" stroke="#fff" stroke-width="3.5" stroke-linecap="round"/></svg>
      LOREM IPSUM
    </div>
    <div class="feature" style="left:732px">
      <svg viewBox="0 0 38 38"><circle cx="19" cy="19" r="11" fill="none" stroke="#fff" stroke-width="6" stroke-dasharray="5 3.6"/><circle cx="19" cy="19" r="9" fill="none" stroke="#fff" stroke-width="4"/></svg>
      LOREM IPSUM
    </div>
    <div class="feature" style="left:818px">
      <svg viewBox="0 0 38 38"><path d="M6 32 L32 6" stroke="#fff" stroke-width="4" stroke-linecap="round"/><path d="M8 6 L32 30" stroke="#fff" stroke-width="4" stroke-linecap="round"/><circle cx="8" cy="8" r="5" fill="none" stroke="#fff" stroke-width="3"/></svg>
      LOREM IPSUM
    </div>
  </section>

</main>
</body>
</html>
```